The design should look similar to the uploaded example to accommodate the information needed for a business card template. I would like to see the colors orange and charcoal grey incorporated along with the logo.The following should be on the back of the card SPECIALIZING IN NEW AND USED TIRES & WHEELS FOR:- Loaders- Skid Steers- Telehandlers- Boom Lifts- Forklifs and moreELIMINATING DOWNTIMEWheel Exchange Program for New & Used Foam Filled and Solid Rubber TiresSPECIALTY SERVICES- Foam Filling Tires- Largest Tire Press in SE- ONSITE Forklift Tire Press- Boom Truck Services - Rubber Tracks

Target Market(s)

New and Existing Customers

Industry/Entity Type

Business

Contact Information for Business Card

NAMEHEAVY DUTY TIRE, LLC8470 Belvedere RoadWest Palm Beach, FL 33411P: 844-HD-TIRESF: 561-431-6469C:E: W: WWW.GRANITERIMSUPPLY-EXAMPLE.COM

Font styles to use
Sans Serif

Colors
f37122
333333

Requirements
Must have
• The logo and the information indicated for the backside of the card
Nice to have
• Keep the orange and charcoal grey colors

```html
<!DOCTYPE html>
<html lang="en">
<head>
<meta charset="utf-8">
<title>Granite Rim Supply – Business Card</title>
<link rel="stylesheet" href="https://fonts.googleapis.com/css2?family=Open+Sans:wght@400;600;700&display=swap">
<style>
  :root {
    --orange: #f37122;
    --orange-soft: #f58a3c;
    --charcoal: #333333;
    --paper: #f4f4f2;
    --backdrop: #2c2927;
    --white: #ffffff;
  }
  * { margin: 0; padding: 0; box-sizing: border-box; }
  html, body { width: 1200px; height: 844px; overflow: hidden; }
  body {
    background: var(--backdrop);
    font-family: "Open Sans", Arial, sans-serif;
    position: relative;
  }
  .card {
    position: absolute;
    top: 262px;
    width: 560px;
    height: 320px;
    border-radius: 2px;
  }
  .card-front { left: 28px; background: var(--paper); color: var(--charcoal); }
  .card-back { left: 612px; background: var(--orange-soft); color: var(--white); text-align: center; overflow: hidden; }

  /* front */
  .contact { position: absolute; left: 40px; top: 44px; }
  .person-name { color: var(--orange); font-size: 22px; font-weight: 600; }
  .company-name { color: var(--orange); font-size: 16px; font-weight: 400; margin-top: 10px; }
  .address { font-size: 15px; line-height: 21px; margin-top: 4px; }
  .contact-list { list-style: none; margin-top: 20px; font-size: 15px; }
  .contact-list li { display: flex; align-items: center; height: 22px; }
  .contact-list svg { width: 12px; height: 12px; margin-right: 14px; fill: var(--orange); flex: none; }
  .brand {
    position: absolute; right: 44px; top: 74px; width: 170px;
    display: flex; flex-direction: column; align-items: center;
  }
  .brand-dot { width: 120px; height: 120px; border-radius: 50%; background: var(--orange); }
  .brand-name { margin-top: 12px; font-size: 20px; font-weight: 700; color: var(--charcoal); letter-spacing: 1px; }

  /* back */
  .back-mark {
    position: absolute; left: 50%; top: 50%; width: 260px; height: 260px;
    transform: translate(-50%, -50%); border-radius: 50%;
    background: rgba(0,0,0,0.06);
  }
  .back-content { position: relative; padding-top: 36px; }
  .back-heading { font-size: 15px; font-weight: 600; }
  .back-line { font-size: 12.5px; line-height: 19px; }
  .back-heading + .back-line { margin-top: 8px; }
  .back-subheading { font-size: 12.5px; margin-top: 14px; }
  .back-section-title { font-size: 16px; font-weight: 600; margin-top: 16px; }
  .bullet { display: inline-block; width: 6px; height: 6px; border-radius: 50%; background: var(--white); margin: 0 10px; vertical-align: middle; }
</style>
</head>
<body>
  <section class="card card-front">
    <div class="contact">
      <h1 class="person-name">Marcus Delaney</h1>
      <p class="company-name">GRANITE RIM SUPPLY, LLC</p>
      <p class="address">5126 Marston Lane<br>Port Halden, FL 33920</p>
      <ul class="contact-list">
        <li><svg viewBox="0 0 12 12"><path d="M2 1l2 0 1 3-1.5 1a6 6 0 003.5 3.5L8 7l3 1v2a1 1 0 01-1 1A9 9 0 011 2a1 1 0 011-1z"/></svg>844-GR-WHEEL</li>
        <li><svg viewBox="0 0 12 12"><rect x="3" y="0" width="6" height="4"/><rect x="0" y="4" width="12" height="6" rx="1"/><rect x="3" y="8" width="6" height="4"/></svg>561-278-9053</li>
        <li><svg viewBox="0 0 12 12"><rect x="3" y="0" width="6" height="12" rx="1"/></svg>123-456-7890</li>
        <li><svg viewBox="0 0 12 12"><path d="M0 2h12v8H0z M0 2l6 5 6-5" /></svg>info@graniterimsupply-example.com</li>
        <li><svg viewBox="0 0 12 12"><circle cx="6" cy="6" r="6"/></svg>www.graniterimsupply-example.com</li>
      </ul>
    </div>
    <div class="brand">
      <div class="brand-dot"></div>
      <p class="brand-name">GRANITE RIM</p>
    </div>
  </section>

  <section class="card card-back">
    <div class="back-mark"></div>
    <div class="back-content">
      <h2 class="back-heading">SPECIALIZING IN NEW AND USED TIRES &amp; WHEELS FOR:</h2>
      <p class="back-line">Loaders<span class="bullet"></span>Skid Steers<span class="bullet"></span>Telehandlers<span class="bullet"></span>Boom Lifts</p>
      <p class="back-line">Forklifs and more</p>
      <p class="back-line back-subheading">ELIMINATING DOWNTIME</p>
      <p class="back-line">Wheel Exchange Program for New &amp; Used Foam</p>
      <p class="back-line">Filled and Solid Rubber Tires</p>
      <h2 class="back-section-title">SPECIALTY SERVICES</h2>
      <p class="back-line">Foam Filling Tires<span class="bullet"></span>Largest Tire Press in SE</p>
      <p class="back-line">ONSITE Forklift Tire Press<span class="bullet"></span>Boom Truck Services<span class="bullet"></span>Rubber Tracks</p>
    </div>
  </section>
</body>
</html>
```